Presentation Box for dry goods meat product

We would like a box designed for presentation on a shelf. Our product is fully cooked meats (beef, pork and chicken) that has a 12- to 18-month shelf-life without refrigeration. It's not dried food, but because of the cooking process it's succulent meat in sauce, storable at room temperature.Our anchor product will be "Timber Hollow Smoke Pot."The dimensions for the box will be approximately 8" tall by 5" wide and 2.5" deep.We have an oval-shaped (horizontal) logo in Navy, Crimson and Old Gold (think Dunmore Lanterns colors).
Updates

Reason: We haven't received enough options. We want the design to say "Timber Hollow Style Smoke Pot" not "Timber Hollow Smoke Pot." Use pictures of beef brisket (not steaks), pulled pork (not pork chops) and pulled chicken (not chicken legs/thighs).

Target Market(s)

Meat-buying consumers

Industry/Entity Type

Cooking

Requirements
Must have
• Space for ingredients and nutrition information. The name of our company is Merrow Foods.
Nice to have
• Picture of Bar-B-Que beef, pork and chicken

```html
<!DOCTYPE html>
<html lang="en">
<head>
<meta charset="utf-8">
<title>Merrow Foods – Timber Hollow Style Smoke Pot Box</title>
<link rel="stylesheet" href="https://fonts.googleapis.com/css2?family=Oswald:wght@500;700&family=Alfa+Slab+One&display=swap">
<style>
  :root {
    --page: #ececec;
    --navy: #1c2a44;
    --navy-deep: #111a2c;
    --cream: #f4ecd6;
    --crimson: #8c1d24;
    --crimson-dark: #5e1016;
    --gold: #f0b429;
    --flame-orange: #f26a1b;
    --flame-red: #b8280f;
    --ember: #3a1a0c;
    --white: #ffffff;
    --rule: #c9d0dc;
  }
  * { box-sizing: border-box; margin: 0; padding: 0; }
  html, body {
    width: 1079px; height: 1200px; overflow: hidden;
    background: var(--page);
  }
  .canvas { position: relative; width: 1079px; height: 1200px; }

  .panel { position: absolute; background: var(--navy); overflow: hidden; }
  .panel-top   { left: 209px; top: 138px; width: 440px; height: 220px; background: var(--navy-deep); }
  .panel-front { left: 209px; top: 358px; width: 440px; height: 704px; }
  .panel-side  { left: 649px; top: 358px; width: 220px; height: 704px; background: var(--navy-deep); }

  .brand-name {
    font-family: "Oswald", sans-serif; font-weight: 700;
    color: var(--navy); line-height: 1; text-align: center;
  }

  /* top face */
  .top-brand { position: absolute; left: 0; right: 0; top: 40px; font-size: 26px; color: var(--cream); }
  .top-style {
    position: absolute; left: 0; right: 0; top: 88px; text-align: center;
    font-family: "Oswald", sans-serif; font-weight: 700; font-size: 26px; color: var(--white);
  }
  .top-product {
    position: absolute; left: 0; right: 0; top: 128px; text-align: center;
    font-family: "Alfa Slab One", serif; font-size: 40px; color: var(--flame-orange);
  }

  /* front face */
  .brand-label {
    position: absolute; left: 70px; top: 40px; width: 300px; height: 120px;
    background: var(--cream); border-radius: 14px;
    display: flex; align-items: center; justify-content: center;
  }
  .brand-label .brand-name { font-size: 52px; }
  .brand-band {
    position: absolute; left: 100px; top: 160px; width: 240px; height: 70px;
    background: linear-gradient(180deg, var(--crimson), var(--crimson-dark));
  }
  .product-style {
    position: absolute; left: 0; right: 0; top: 252px; text-align: center;
    font-family: "Oswald", sans-serif; font-weight: 700; font-size: 36px;
    color: var(--white); text-shadow: 2px 3px 4px rgba(0,0,0,.6);
  }
  .product-name {
    position: absolute; left: 0; right: 0; top: 305px; text-align: center;
    font-family: "Alfa Slab One", serif; font-size: 58px; line-height: 1;
    color: var(--flame-orange); text-shadow: 2px 2px 0 var(--crimson), 3px 5px 6px rgba(0,0,0,.6);
  }
  .window {
    position: absolute; left: 100px; top: 390px; width: 240px; height: 120px;
    background: #07090f;
  }
  .grill-photo {
    position: absolute; left: 0; right: 0; bottom: 0; height: 250px;
    background:
      radial-gradient(ellipse 70% 45% at 50% 70%, #9a6a4a 0%, #6b3e24 45%, transparent 75%),
      linear-gradient(180deg, transparent 0%, var(--flame-red) 25%, var(--flame-orange) 55%, var(--ember) 100%);
  }

  /* side face */
  .side-brand { position: absolute; left: 0; right: 0; top: 40px; font-size: 30px; color: var(--cream); }
  .info-heading {
    position: absolute; left: 22px;
    font-family: "Oswald", sans-serif; font-weight: 500; font-size: 15px; color: var(--gold);
  }
  .info-heading.nutrition { top: 130px; }
  .info-heading.ingredients { top: 330px; }
  .info-lines { position: absolute; left: 22px; width: 176px; }
  .info-lines.nutrition { top: 162px; }
  .info-lines.ingredients { top: 362px; }
  .info-lines span { display: block; height: 1px; background: var(--rule); margin-bottom: 15px; }
  .side-photo {
    position: absolute; left: 0; right: 0; bottom: 0; height: 250px;
    background:
      radial-gradient(ellipse 70% 40% at 55% 70%, #9a6a4a 0%, #6b3e24 45%, transparent 75%),
      linear-gradient(180deg, transparent 0%, var(--flame-red) 25%, var(--flame-orange) 55%, var(--ember) 100%);
  }
</style>
</head>
<body>
<main class="canvas">
  <section class="panel panel-top">
    <p class="brand-name top-brand">Merrow Foods</p>
    <p class="top-style">Timber Hollow Style</p>
    <p class="top-product">SMOKE POT</p>
  </section>

  <section class="panel panel-front">
    <div class="brand-label"><p class="brand-name">Merrow Foods</p></div>
    <div class="brand-band"></div>
    <h2 class="product-style">Timber Hollow Style</h2>
    <h1 class="product-name">SMOKE POT</h1>
    <div class="window"></div>
    <div class="grill-photo" role="img" aria-label="Barbecued meats on a grill over open flames"></div>
  </section>

  <section class="panel panel-side">
    <p class="brand-name side-brand">Merrow Foods</p>
    <h3 class="info-heading nutrition">Nutrition information</h3>
    <div class="info-lines nutrition"><span></span><span></span><span></span><span></span><span></span><span></span><span></span><span></span><span></span><span></span></div>
    <h3 class="info-heading ingredients">Ingredients</h3>
    <div class="info-lines ingredients"><span></span><span></span><span></span><span></span><span></span><span></span><span></span></div>
    <div class="side-photo" role="img" aria-label="Grilled barbecue meat over flames"></div>
  </section>
</main>
</body>
</html>
```